Zestora - Landing Page

Need a landing page for a journal app. The app is based on a retrospective board, where each journal entry is split into 3 sections: "What went well", "What Didn't Go Well" and "Things To Try".
The landing page should match the style of all modern web application landing pages. Think Brint, Tivalo, Mirvane. I've included screenshots of the app.
One feature that I want to highlight that is not ready yet, is an AI coach. It will offer insights based on the history of the user's journal entries
1 page

```html
<!DOCTYPE html>
<html lang="en">
<head>
<meta charset="utf-8">
<title>Zestora – Mindful Journaling</title>
<link href="https://fonts.googleapis.com/css2?family=Poppins:wght@400;500;600;700;800&display=swap" rel="stylesheet">
<style>
:root{
  --blue:#0a5bd6;
  --blue-deep:#0048b8;
  --ink:#111418;
  --muted:#6b7078;
  --line:#dde2ea;
  --soft:#f4f7fc;
  --white:#ffffff;
  --black:#0d0d0d;
  --side:#1f2937;
}
*{box-sizing:border-box;margin:0;padding:0}
html,body{width:1200px;height:3468px;overflow:hidden}
body{position:relative;font-family:'Poppins',sans-serif;color:var(--ink);background:var(--white)}
.abs{position:absolute}
a{color:inherit;text-decoration:none}

/* nav */
.brand{display:flex;align-items:center;gap:10px;font-weight:800;font-size:28px;letter-spacing:1px;color:var(--ink)}
.brand-dot{width:28px;height:28px;border-radius:50%;background:var(--blue)}
.nav{left:40px;top:22px;width:1120px;height:50px;display:flex;align-items:center;justify-content:space-between}
.nav-links{display:flex;gap:48px;font-size:15px;font-weight:500;margin-left:120px}
.nav-links .active{color:var(--blue);border-bottom:2px solid var(--blue);padding-bottom:3px}
.btn{display:inline-flex;align-items:center;justify-content:center;background:var(--blue);color:var(--white);font-weight:600;font-size:15px;border-radius:24px;height:42px;padding:0 24px}
.btn-outline{background:var(--white);color:var(--blue)}

/* hero */
.hero-title{left:0;width:1200px;top:135px;text-align:center;font-size:44px;font-weight:800}
.hero-title span{color:var(--blue)}
.hero-sub{left:0;width:1200px;top:205px;text-align:center;font-size:17px;color:#333}
.hero-cta{left:525px;top:258px;width:150px}
.partners{left:120px;top:335px;width:960px;display:flex;justify-content:space-between;align-items:center;font-weight:600;font-size:22px;color:#333}

.circle{border-radius:50%;background:var(--blue)}

/* mockup board */
.board{background:var(--white);border-radius:14px;box-shadow:0 10px 40px rgba(10,40,90,.18);display:flex;overflow:hidden}
.board-side{width:26px;background:var(--side)}
.board-main{flex:1;padding:14px 16px;display:flex;flex-direction:column}
.board-title{font-size:13px;font-weight:600}
.board-date{font-size:9px;color:var(--muted);margin:4px 0 10px}
.cols{flex:1;display:flex;gap:16px}
.col{flex:1;border:1px solid var(--line);border-radius:6px;padding:8px;font-size:9px;color:#333}
.col h4{font-size:9px;font-weight:600;margin-bottom:8px}
.col ul{padding-left:12px;line-height:1.5}
.tag{display:inline-block;font-size:7px;background:#e7efff;border-radius:3px;padding:1px 5px;margin-bottom:6px}

/* offer */
.section-title{left:0;width:1200px;text-align:center;font-size:36px;font-weight:800}
.section-lead{left:140px;width:920px;text-align:center;font-size:14px;color:#444;line-height:1.6}
.feature-text h3{font-size:21px;font-weight:700;margin-bottom:12px}
.feature-text p{font-size:13px;color:var(--muted);line-height:1.6;margin-bottom:18px}
.feature-text .btn{height:38px;font-size:13px;padding:0 22px}
.step{width:40px;height:40px;border-radius:50%;border:2px solid var(--blue);background:var(--white);color:var(--blue);font-size:13px;font-weight:700;display:flex;align-items:center;justify-content:center}

/* band */
.band{left:0;top:2200px;width:1200px;height:350px;background:var(--blue);color:var(--white);text-align:center}
.band h2{font-size:32px;font-weight:700;line-height:1.4;margin-top:60px}
.band .stats{margin-top:18px;font-size:16px}
.band .stats b{font-weight:700;margin-right:8px}
.band .stars{letter-spacing:2px;margin-right:8px}
.band .actions{margin-top:28px;display:flex;gap:16px;justify-content:center}
.band .btn{height:40px;font-size:14px}
.band .btn-dark{background:var(--blue-deep);border:1px solid rgba(255,255,255,.4)}

/* coach */
.coach-art{left:130px;top:2765px;width:470px;height:280px;border-radius:10px;background:linear-gradient(160deg,#2b2f36,#5a6270)}
.coach-text{left:640px;top:2770px;width:440px;font-size:14px;color:#444;line-height:1.7}
.coach-text p{margin-bottom:16px}

/* footer */
.footer{left:0;top:3220px;width:1200px;height:248px;background:var(--black);color:var(--white);text-align:center}
.footer .brand{color:var(--white);justify-content:center;margin-top:48px}
.footer-links{display:flex;justify-content:center;gap:70px;font-size:14px;margin-top:26px}
.socials{display:flex;justify-content:center;gap:12px;margin-top:22px}
.socials span{width:30px;height:30px;border-radius:50%;background:var(--blue)}
.copy{font-size:12px;margin-top:20px;color:#ccc}
</style>
</head>
<body>

<header class="abs nav">
  <div class="brand"><span class="brand-dot"></span>ZESTORA</div>
  <nav class="nav-links">
    <a class="active">Home</a><a>About Us</a><a>Services</a><a>Reviews</a><a>Blogs</a>
  </nav>
  <a class="btn">Contact Us</a>
</header>

<h1 class="abs hero-title">Mindful Journaling <span>Starts Here</span></h1>
<p class="abs hero-sub">Find peace and clarity with every entry. Your path to mindfulness begins now.</p>
<a class="abs btn hero-cta">Start For Free</a>

<div class="abs partners">
  <span>Loftly</span><span>Veramed</span><span>Northline</span><span>Carewell</span><span>Hublane</span>
</div>

<div class="abs circle" style="left:40px;top:420px;width:150px;height:150px"></div>
<div class="abs circle" style="left:1010px;top:820px;width:170px;height:170px"></div>

<div class="abs board" style="left:132px;top:412px;width:940px;height:548px">
  <div class="board-side"></div>
  <div class="board-main">
    <div class="board-title">Entry</div>
    <div class="board-date">Thu Aug 15, 2024</div>
    <div class="cols">
      <div class="col"><h4>What Went Well?</h4><ul><li>Completed all scheduled workouts this week.</li><li>Increased bench press weight by 10 pounds.</li><li>Kept steady energy levels through sessions.</li></ul></div>
      <div class="col"><h4>What Didn't Go Well?</h4><ul><li>Struggled with form on deadlifts, causing back strain.</li><li>Missed two stretching sessions after workouts.</li><li>Skipped meal prep, so nutrition slipped.</li></ul></div>
      <div class="col"><h4>Things To Try</h4><ul><li>Focus on deadlift form and review technique.</li><li>Set reminders for post-workout stretching.</li><li>Use Sunday mornings for meal prep.</li></ul></div>
    </div>
  </div>
</div>

<h2 class="abs section-title" style="top:1010px">What We Offer</h2>
<p class="abs section-lead" style="top:1065px">Denounce with righteous indignation and dislike men who are so beguiled and demoralized by the charms of pleasure of the moment, so blinded by desire, that they cannot foresee the pain and trouble.</p>

<!-- feature 1 -->
<div class="abs circle" style="left:30px;top:1150px;width:130px;height:130px"></div>
<div class="abs board" style="left:90px;top:1170px;width:510px;height:230px">
  <div class="board-side"></div>
  <div class="board-main"><div class="board-title">Entry</div><div class="board-date">Thu Aug 15</div>
    <div class="cols"><div class="col"><h4>Went Well</h4></div><div class="col"><h4>Not Well</h4></div><div class="col"><h4>To Try</h4></div></div></div>
</div>
<div class="abs step" style="left:620px;top:1305px">01</div>
<div class="abs feature-text" style="left:710px;top:1220px;width:380px">
  <h3>What Went Well</h3>
  <p>Lorem ipsum dolor sit amet, consectetur adipiscing elit, sed do eiusmod tempor incididunt ut labore et dolore magna aliqua.</p>
  <a class="btn">View Details</a>
</div>

<!-- feature 2 -->
<div class="abs circle" style="left:1070px;top:1380px;width:130px;height:130px"></div>
<div class="abs feature-text" style="left:250px;top:1555px;width:300px;text-align:right">
  <h3>What Didn't Go Well</h3>
  <p>Lorem ipsum dolor sit amet, consectetur adipiscing elit, sed do eiusmod tempor incididunt ut labore et dolore magna aliqua.</p>
  <a class="btn">View Details</a>
</div>
<div class="abs step" style="left:560px;top:1500px">02</div>
<div class="abs board" style="left:630px;top:1415px;width:520px;height:240px">
  <div class="board-side"></div>
  <div class="board-main"><div class="board-title">Entry</div><div class="board-date">Thu Aug 15</div>
    <div class="cols"><div class="col"><h4>Went Well</h4></div><div class="col"><h4>Not Well</h4></div><div class="col"><h4>To Try</h4></div></div></div>
</div>

<!-- feature 3 -->
<div class="abs circle" style="left:50px;top:1960px;width:140px;height:140px"></div>
<div class="abs board" style="left:110px;top:1820px;width:490px;height:285px">
  <div class="board-side"></div>
  <div class="board-main"><div class="board-title">Things To Try</div><div class="board-date">Thu Aug 15</div>
    <div class="col" style="flex:1"><span class="tag">Fitness</span><ul><li>Review deadlift technique</li><li>Stretch after each workout</li><li>Prep meals on Sunday</li></ul></div></div>
</div>
<div class="abs step" style="left:620px;top:1940px">03</div>
<div class="abs feature-text" style="left:710px;top:1870px;width:380px">
  <h3>Things To Try</h3>
  <p>Lorem ipsum dolor sit amet, consectetur adipiscing elit, sed do eiusmod tempor incididunt ut labore et dolore magna aliqua.</p>
  <a class="btn">View Details</a>
</div>

<section class="abs band">
  <h2>Gain calmness and clarity with the world's<br>most beloved productivity app</h2>
  <div class="stats"><b>374000+</b><span class="stars">★★★★★</span>reviews on Playhub and Appvault</div>
  <div class="actions"><a class="btn btn-dark">Start For Free</a><a class="btn btn-outline">Download App</a></div>
</section>

<h2 class="abs section-title" style="top:2680px">AI Coach</h2>
<div class="abs circle" style="left:90px;top:2800px;width:270px;height:270px"></div>
<div class="abs coach-art" role="img" aria-label="Laptop showing the Zestora journal board with the AI coach"></div>
<div class="abs coach-text">
  <p>I must explain to you how all this mistaken idea of denouncing pleasure and praising pain was born and I will give you a complete account of the system.</p>
  <p>Expound the actual teachings of the great explorer of the truth, the master-builder of human happiness. No one rejects, dislikes, or avoids pleasure itself, because it is pleasure, but because those who.</p>
  <a class="btn" style="height:38px;font-size:13px">Read More</a>
</div>

<footer class="abs footer">
  <div class="brand"><span class="brand-dot"></span>ZESTORA</div>
  <div class="footer-links"><a>Home</a><a>About Us</a><a>Services</a><a>Reviews</a><a>Blogs</a><a>Contact Us</a></div>
  <div class="socials"><span></span><span></span><span></span><span></span></div>
  <div class="copy">(c) Copyright 2024 | All Rights Reserved</div>
</footer>

</body>
</html>
```